Website Design for Landscaping/Concrete Company

I need a website that is informative about what my company does and also offers before and after pictures of completed work. I already have a logo. The website must say "FREE ESTIMATES" somewhere and list a phone number. I would like to stick with the logo colors or similar (black and lime green).
Services Offered by Tomlet Builders:
Landscaping
Mowing
Concrete
Sidewalks
Brush Removal
Land Beautification

Please list the company name in large letters TOMLET BUILDERS
and also the contact information in large font.

Right now I am looking for a somewhat coverpage for my website. I don't have a lot of information for people to point and click on yet. Id like to get a coverpage to get my name out and then have a designer come back in a few months and update with more pictures and information.
Updates

If allowed please submit projects after due date. I made a mistake and only posted for one day. Thanks.

Coding

Coded - Design and coding required

```html
<!DOCTYPE html>
<html lang="en">
<head>
<meta charset="utf-8">
<title>Tomlet Builders – Landscaping &amp; Concrete</title>
<link rel="stylesheet" href="https://fonts.googleapis.com/css2?family=Rajdhani:wght@500;600;700&family=Mulish:ital,wght@0,400;0,600;1,400&display=swap">
<style>
:root{
  --black:#000;
  --coal:#141414;
  --lime:#9acb1f;
  --olive:#7fa414;
  --white:#fff;
  --grey:#bdbdbd;
  --field:#f4f4f4;
}
*{box-sizing:border-box;margin:0;padding:0}
html,body{width:1200px;height:5396px;overflow:hidden;background:var(--black)}
body{position:relative;font-family:"Mulish",sans-serif;color:var(--white)}
.abs{position:absolute}
.display{font-family:"Rajdhani",sans-serif;font-weight:700;line-height:1}
.lime{color:var(--lime)}

/* header */
.site-header{left:0;top:0;width:1200px;height:161px;background:var(--black)}
.brand{left:172px;top:66px;display:flex;align-items:center;gap:10px;font-family:"Rajdhani",sans-serif;font-weight:700;font-size:22px;color:var(--lime);letter-spacing:1px}
.brand-square{width:16px;height:16px;background:var(--lime)}
.estimate{left:551px;top:26px;font-size:38px;color:var(--lime);letter-spacing:.5px}
.main-nav{left:335px;top:98px;display:flex;gap:0;font-size:15px;color:#d8d8d8}
.main-nav a{color:inherit;text-decoration:none;margin-right:44px}
.main-nav a.active{color:var(--lime)}

/* hero */
.hero{left:0;top:161px;width:1200px;height:650px;background:linear-gradient(180deg,#34591c 0%,#4f8a24 35%,#6fae2c 70%,#5a9922 100%)}
.hero-title{left:0;width:1200px;text-align:center;color:var(--white)}
.hero-title.one{top:410px;font-size:140px}
.hero-title.two{top:560px;font-size:96px;letter-spacing:2px}
.dots{left:583px;top:729px;display:flex;gap:4px}
.dots i{width:6px;height:6px;border-radius:50%;background:var(--white);display:block}

/* about */
.about-photo{left:268px;top:848px;width:272px;height:426px;background:linear-gradient(160deg,#8b8b84,#4f7f2a 70%,#2e4d17);clip-path:polygon(50% 0,100% 25%,100% 75%,50% 100%,0 75%,0 25%)}
.about-title{left:620px;top:912px;font-size:46px;color:var(--lime)}
.about-text{left:620px;top:1018px;width:410px;font-size:12.5px;line-height:23px;color:var(--grey)}

/* services */
.services{left:0;top:1383px;width:1200px;height:968px;background:linear-gradient(160deg,#1c1c1c,#0e0e0e)}
.section-title{left:0;width:1200px;text-align:center;font-size:44px}
.card{width:270px;height:314px}
.card-photo{position:absolute;left:0;top:0;width:270px;height:163px}
.card-body{position:absolute;left:21px;top:163px;width:249px;height:151px;background:var(--olive);padding:22px 0 0 30px}
.card-body h3{font-family:"Rajdhani",sans-serif;font-weight:700;font-size:27px;line-height:1;color:var(--white);margin-bottom:10px}
.card-body p{font-size:13px;line-height:20px;color:#eef5d8;width:195px}

/* works */
.works{left:0;top:2351px;width:1200px;height:752px;background:linear-gradient(100deg,#7aa23a 0%,#a4c85a 40%,#4c7a22 75%,#375b1c 100%)}
.works-panel{left:132px;top:2501px;width:457px;height:482px;background:rgba(10,10,10,.88);padding:70px 46px 0 48px}
.works-panel h2{font-size:44px;margin-bottom:20px}
.works-panel p{font-size:12.5px;line-height:23px;color:#cfcfcf}
.works-dots{display:flex;gap:14px;margin-top:28px}
.works-dots i{width:15px;height:15px;border-radius:50%;background:#8a8a8a;display:block}
.works-dots i:first-child{background:var(--lime)}

/* why */
.why-photo{left:394px;top:3268px;width:306px;height:478px;background:linear-gradient(170deg,#5f9128,#8e8c85 50%,#3f6e1e);clip-path:polygon(50% 0,100% 25%,100% 75%,50% 100%,0 75%,0 25%)}
.reason{width:300px}
.reason h4{font-family:"Rajdhani",sans-serif;font-weight:700;font-size:15px;color:var(--lime);letter-spacing:.5px}
.reason p{font-size:12.5px;line-height:18px;color:var(--grey)}
.reason .num{position:absolute;top:-4px;font-family:"Rajdhani",sans-serif;font-weight:700;font-size:46px;color:var(--lime);line-height:1}
.reason.left{text-align:right}
.reason.left .num{right:-40px}
.reason.right{padding-left:0}
.reason.right .num{left:-40px}

/* testimonial */
.testimonial{left:0;top:3770px;width:1200px;height:580px;background:linear-gradient(110deg,#2f3326,#3e4a2e 50%,#23281d)}
.quote-mark{left:210px;top:3950px;font-family:"Rajdhani",sans-serif;font-weight:700;font-size:170px;line-height:1;color:var(--lime)}
.quote-text{left:323px;top:3972px;width:580px;font-style:italic;font-size:18.5px;line-height:26px;color:#ededed}
.quote-author{left:323px;top:4150px;font-family:"Rajdhani",sans-serif;font-weight:700;font-size:16px;color:var(--lime)}
.arrows{left:890px;top:4164px}

/* contact */
.contact{left:0;top:4326px;width:1200px;height:620px;background:linear-gradient(180deg,#0c0c0c,#141414)}
.contact-intro{left:0;width:1200px;top:4484px;text-align:center;font-size:12.5px;line-height:23px;color:var(--grey)}
.field{background:var(--field);color:#444;font-size:11px;padding:8px 18px}
.submit{left:538px;top:4781px;width:124px;height:50px;border-radius:25px;background:var(--olive);font-family:"Rajdhani",sans-serif;font-weight:700;font-size:14px;text-align:center;line-height:50px}

/* footer */
.site-footer{left:0;top:4944px;width:1200px;height:452px;background:#050505}
.footer-badge{left:458px;top:4880px;width:284px;height:284px;border-radius:50%;background:#0b0b0b}
.footer-brand{left:0;width:1200px;top:5000px;text-align:center;font-family:"Rajdhani",sans-serif;font-weight:700;font-size:40px;color:#cfcfcf;letter-spacing:2px}
.contact-item{width:300px;text-align:center;font-size:15px;line-height:22px;color:#e8e8e8}
.contact-item .icon{width:34px;height:34px;border-radius:50%;background:var(--olive);margin:0 auto 10px;display:flex;align-items:center;justify-content:center}
.contact-item a{color:#e8e8e8}
.socials{left:515px;top:5306px;display:flex;gap:26px}
.socials i{width:20px;height:20px;border-radius:50%;border:2px solid #e8e8e8;display:block}
.copyright{left:0;width:1200px;top:5350px;text-align:center;font-size:15px;color:#e0e0e0}
</style>
</head>
<body>

<header class="abs site-header">
  <div class="abs brand"><span class="brand-square"></span>TOMLET BUILDERS</div>
  <div class="abs estimate display">FREE ESTIMATES&nbsp; 0400 123 456</div>
  <nav class="abs main-nav">
    <a class="active" href="#">Home</a><a href="#">About Us</a><a href="#">Services</a><a href="#">Projects</a><a href="#">Why Us</a><a href="#">Testimonials</a><a href="#">Contact Us</a>
  </nav>
</header>

<section class="abs hero" role="img" aria-label="Lush garden lawn with a curved paver footpath"></section>
<h1 class="abs hero-title one display">TOMLET</h1>
<div class="abs hero-title two display">BUILDERS</div>
<div class="abs dots"><i></i><i></i><i></i><i></i></div>
<svg class="abs" style="left:0;top:760px" width="1200" height="60" viewBox="0 0 1200 60">
  <polygon points="0,46 1200,8 1200,60 0,60" fill="#000"/>
  <polygon points="0,46 1200,8 1200,20 0,52" fill="#9acb1f"/>
</svg>

<section class="abs about-photo" role="img" aria-label="Paved path and hedges framed in an angular panel"></section>
<h2 class="abs about-title display">ABOUT<br>TOMLET BUILDERS</h2>
<p class="abs about-text">Lorem ipsum dolor sit amet, consectetur adipiscing elit, sed do eiusmod tempor incididunt ut labore et dolore magna aliqua. Ut enim ad minim veniam, quis nostrud exercitation ullamco laboris nisi ut aliquip ex ea commodo consequat. Duis aute irulore dolor in reprehenderitn voluptat laboris nisi ut aliquip ex lolea commodo consequat. Duis aute irat. Duis aute irure dlaolor ilon reprehenditn voluptat laboris nisi ut aliquip ex ea commodolor consequat.is autesi ut aliquip ex quat. Duis aute irat. Duis aute irure dlaolor ilon reprehenditn voluptatea co.</p>

<section class="abs services">
  <h2 class="abs section-title display lime" style="top:110px">WE OFFER SERVICES</h2>

  <article class="abs card" style="left:172px;top:184px">
    <div class="card-photo" role="img" aria-label="Landscaped garden bed with flowers" style="background:linear-gradient(160deg,#8fb2d6,#6aa33a 55%,#3d7a20)"></div>
    <div class="card-body"><h3>Landscaping</h3><p>Lorem ipsum dolor sit amet consectetur adipiscing elit eiusmod tempor...</p></div>
  </article>
  <article class="abs card" style="left:465px;top:184px">
    <div class="card-photo" role="img" aria-label="Lawn mower on fresh cut grass" style="background:linear-gradient(160deg,#3a5a24,#5f8f2d 55%,#7fb23a)"></div>
    <div class="card-body"><h3>Mowing</h3><p>Lorem ipsum dolor sit amet consectetur adipiscing elit eiusmod tempor...</p></div>
  </article>
  <article class="abs card" style="left:756px;top:184px">
    <div class="card-photo" role="img" aria-label="Concrete being poured on a site" style="background:linear-gradient(160deg,#9a9890,#6f6d66 55%,#8c7f62)"></div>
    <div class="card-body"><h3>Concrete</h3><p>Lorem ipsum dolor sit amet consectetur adipiscing elit eiusmod tempor...</p></div>
  </article>

  <article class="abs card" style="left:172px;top:536px">
    <div class="card-photo" role="img" aria-label="Curved brick sidewalk through a lawn" style="background:linear-gradient(170deg,#4f8a2a,#b29c86 55%,#6ea33a)"></div>
    <div class="card-body"><h3>Sidewalks</h3><p>Lorem ipsum dolor sit amet consectetur adipiscing elit eiusmod tempor...</p></div>
  </article>
  <article class="abs card" style="left:465px;top:536px">
    <div class="card-photo" role="img" aria-label="Broom and rake on green grass" style="background:linear-gradient(160deg,#2f5a1c,#4f8a2a 60%,#c0703a)"></div>
    <div class="card-body"><h3>Brush Removal</h3><p>Lorem ipsum dolor sit amet consectetur adipiscing elit eiusmod tempor...</p></div>
  </article>
  <article class="abs card" style="left:756px;top:536px">
    <div class="card-photo" role="img" aria-label="Neatly trimmed hedges" style="background:linear-gradient(160deg,#3f7a1c,#6fb02a 55%,#4c8a22)"></div>
    <div class="card-body"><h3 style="font-size:25px;line-height:22px">Land<br>Beautification</h3><p>Lorem ipsum dolor sit amet consectetur adipiscor...</p></div>
  </article>
</section>

<section class="abs works" role="img" aria-label="Worker trimming long grass with a line trimmer in a park"></section>
<div class="abs works-panel">
  <h2 class="display lime">OUR WORKS</h2>
  <p>Lorem ipsum dolor sit amet, consectetur adipiscing elit, sed do eiusmod tempor incididunt ut labore et dolore magna aliqua. Ut enim ad minim veniam, quis nostrud exercitation ullamco laboris nisi ut aliquip ex ea comm odo consequat. Duis aute irure dolor in reprehenderitn voluptat laboris nisi ut aliquip ex ea commodo conseq uat. Duis aute irre aliqua. Ut enim ad minim veniam, qu is nostrud exercitation ullamco laboris nisi ut aliquip ex ea commodo consequat. Duis aute irure dolor in repr ehenderitn voluptat laboris nisi ut ali</p>
  <div class="works-dots"><i></i><i></i><i></i><i></i></div>
</div>

<h2 class="abs section-title display lime" style="top:3175px">WHY CHOOSE US</h2>
<div class="abs why-photo" role="img" aria-label="Hedges and paving framed in an angular panel"></div>
<div class="abs reason left" style="left:10px;top:3418px"><span class="num">1</span><h4>FINIBUS BONORUM ET</h4><p>Aliquam erat volutpat Quisque dignissim<br>congue leo Mauris vel lacus</p></div>
<div class="abs reason left" style="left:14px;top:3532px"><span class="num">2</span><h4>FINIBUS BONORUM ET</h4><p>Aliquam erat volutpat Quisque dignissim<br>congue leo Mauris vel lacus</p></div>
<div class="abs reason right" style="left:786px;top:3322px"><span class="num">3</span><h4>FINIBUS BONORUM ET</h4><p>Aliquam erat volutpat Quisque dignissim<br>congue leo Mauris vel lacus</p></div>
<div class="abs reason right" style="left:784px;top:3430px"><span class="num">4</span><h4>FINIBUS BONORUM ET</h4><p>Aliquam erat volutpat Quisque dignissim<br>congue leo Mauris vel lacus</p></div>
<div class="abs reason right" style="left:782px;top:3560px"><span class="num">5</span><h4>FINIBUS BONORUM ET</h4><p>Aliquam erat volutpat Quisque dignissim<br>congue leo Mauris vel lacus</p></div>

<section class="abs testimonial" role="img" aria-label="Worker laying paving stones beside a lawn, darkened"></section>
<svg class="abs" style="left:0;top:3770px" width="1200" height="580" viewBox="0 0 1200 580">
  <polygon points="0,0 1200,0 1200,22 0,70" fill="#000"/>
  <polygon points="0,70 1200,22 1200,30 0,92" fill="#9acb1f" opacity=".95"/>
  <polygon points="0,556 1200,480 1200,580 0,580" fill="#0c0c0c"/>
  <polygon points="560,520 1200,466 1200,492 600,532" fill="#9acb1f"/>
</svg>
<div class="abs quote-mark">&ldquo;</div>
<p class="abs quote-text">Sed ut perspiciatis unde omnis iste natus error sit voluptatem accusantium doloremque laudantium, totam rem aperiam, eaque ipsa quae ab illo inventore veritatis et quasi architecto beatae vit ae dicta sunt explicabo. Nemo enim ipsam voluptatem quia volupt as sit aspernatur aut odit aut fugit, sed quia consequuntur eos ratione voluptatem sequi nesciunt.</p>
<div class="abs quote-author">- Jhon Smith City Name</div>
<svg class="abs arrows" width="64" height="48" viewBox="0 0 64 48" aria-label="Previous and next">
  <polyline points="26,4 6,24 26,44" fill="none" stroke="#fff" stroke-width="2"/>
  <polyline points="38,4 58,24 38,44" fill="none" stroke="#fff" stroke-width="2"/>
</svg>

<section class="abs contact">
  <h2 class="abs section-title display" style="top:108px"><span style="color:var(--olive)">GET</span> <span class="lime">IN TOUCH</span></h2>
</section>
<p class="abs contact-intro">Sed ut perspiciatis unde omnis iste natus error sit voluptatem<br>accusantium doloremque laudantium, totam rem aper</p>
<div class="abs field" style="left:331px;top:4580px;width:262px;height:38px">Name:</div>
<div class="abs field" style="left:605px;top:4580px;width:262px;height:38px">Phone:</div>
<div class="abs field" style="left:331px;top:4632px;width:262px;height:38px">Email:</div>
<div class="abs field" style="left:605px;top:4632px;width:262px;height:38px">Subject:</div>
<div class="abs field" style="left:331px;top:4682px;width:536px;height:80px">Message:</div>
<div class="abs submit">SUBMIT HERE</div>

<footer class="abs site-footer"></footer>
<div class="abs footer-badge"></div>
<div class="abs footer-brand">TOMLET BUILDERS</div>

<div class="abs contact-item" style="left:217px;top:5116px">
  <div class="icon"><svg width="16" height="18" viewBox="0 0 16 18"><path d="M8 1a6 6 0 0 1 6 6c0 4-6 10-6 10S2 11 2 7a6 6 0 0 1 6-6z" fill="#fff"/><circle cx="8" cy="7" r="2.2" fill="#7fa414"/></svg></div>
  Tomlet Builders.<br>Dummy Strret Lorem 1141
</div>
<div class="abs contact-item" style="left:449px;top:5116px">
  <div class="icon"><svg width="16" height="16" viewBox="0 0 16 16"><path d="M3 1l3 3-1.5 2.5c1 2 3 4 5 5L12 10l3 3-2 2C7 15 1 9 1 3z" fill="#fff"/></svg></div>
  Phone:<br>0400987654 24/7
</div>
<div class="abs contact-item" style="left:665px;top:5116px">
  <div class="icon"><svg width="18" height="14" viewBox="0 0 18 14"><rect x="1" y="1" width="16" height="12" fill="#fff"/><polyline points="1,1 9,8 17,1" fill="none" stroke="#7fa414" stroke-width="1.5"/></svg></div>
  Email:<br><a href="#">info@tomletbuilders.com</a>
</div>

<div class="abs socials" aria-label="Social links"><i></i><i></i><i></i><i></i></div>
<div class="abs copyright">© 2020 Tomlet Builders. All rights reserved.</div>

</body>
</html>
```